Business card

We need a business card design for our company based in Auckland , New Zealand called 'Ridge + Studio Ltd'. We provide architectural services. We would like to see designs that use the max. three colours (such as white, black, grey) The final design should communicate financial safety and growth."
Also I will provide our company logo. I would like to the logo to be embeded onto our business card.

Target Market(s)

new residential house, alteration & addition & light commericila design & drafting service

Industry/Entity Type

Architecture

Contact Information for Business Card

Company name: ridge + studio Ltd.
Name: Mark Delford
Job title: architectural designer & Design LBP
email address: mark@rplusd.co.nz
mobile number: 02 5163 2290
web site: www.rplusd.co.nz

Requirements
Must have
• My project must have..
• - embeded logo (attached company logo)
• I don't have a bigger version for our company logo, but I have one old one, so you can remove the word from it)
• - insert the attached small BKTW logo & LBP logo
• - creative, simple and clear business card.
• - Max. three colours
Nice to have
• - Here are the samples I would like to share with you: http://www.plimvora.com/blog/minimalistic-business-card-designs/
• I would like to have my business card like one of the creation.
Should not have
• TBA

```html
<!DOCTYPE html>
<html lang="en">
<head>
<meta charset="utf-8">
<title>Ridge + Studio Ltd — Business Card</title>
<link href="https://fonts.googleapis.com/css2?family=Montserrat:wght@400;500;600;700&display=swap" rel="stylesheet">
<style>
  :root {
    --backdrop: #3a3a3a;
    --card: #050505;
    --white: #ffffff;
    --grey: #8a8a84;
    --grey-soft: #5c5c58;
    --text-soft: #d9d9d9;
  }
  * { margin: 0; padding: 0; box-sizing: border-box; }
  html, body { width: 1200px; height: 900px; overflow: hidden; }
  body {
    background: var(--backdrop);
    font-family: "Montserrat", sans-serif;
    color: var(--white);
    position: relative;
  }
  .card {
    position: absolute;
    width: 560px;
    height: 320px;
    background: var(--card);
    border-radius: 26px;
    overflow: hidden;
  }
  .card--front { left: 90px; top: 110px; }
  .card--back { left: 550px; top: 470px; }

  /* Front */
  .brand-front {
    position: absolute;
    left: 60px; top: 70px;
    display: flex; align-items: center; gap: 22px;
  }
  .brand-front .brand-ring {
    width: 120px; height: 120px;
    border: 7px solid var(--white);
    border-radius: 50%;
  }
  .brand-front .brand-name {
    font-size: 30px; font-weight: 600; letter-spacing: 0.5px;
  }
  .front-web {
    position: absolute; left: 202px; top: 222px;
    font-size: 17px; color: var(--text-soft);
  }
  .member {
    position: absolute; right: 120px; top: 200px;
    display: flex; flex-direction: column; align-items: flex-start; gap: 6px;
  }
  .member-badge {
    width: 62px; height: 40px; background: var(--grey-soft); border-radius: 3px;
  }
  .member-label {
    font-size: 13px; font-weight: 600; line-height: 1.15; color: var(--grey);
  }
  .lbp-badge {
    position: absolute; right: 26px; top: 190px;
    width: 76px; height: 76px; border-radius: 50%;
    background: var(--white); border: 4px solid var(--card); outline: 2px solid var(--white);
  }

  /* Back */
  .brand-back {
    position: absolute; left: 40px; top: 0; bottom: 0;
    display: flex; flex-direction: column; justify-content: center; align-items: center; gap: 14px;
    width: 230px;
  }
  .brand-back .brand-ring {
    width: 150px; height: 150px;
    border: 8px solid var(--white); border-radius: 50%;
  }
  .brand-back .brand-name { font-size: 16px; font-weight: 600; }
  .divider {
    position: absolute; left: 300px; top: 55px; width: 1px; height: 210px;
    background: linear-gradient(var(--card), var(--grey) 25%, var(--grey) 75%, var(--card));
  }
  .contact { position: absolute; left: 330px; top: 62px; }
  .person-name { font-size: 26px; font-weight: 700; letter-spacing: 1.5px; }
  .person-title { font-size: 15px; line-height: 1.3; margin-top: 4px; color: var(--text-soft); }
  .contact-list { list-style: none; margin-top: 16px; }
  .contact-list li {
    display: flex; align-items: center; gap: 10px;
    font-size: 15px; line-height: 24px; color: var(--text-soft);
  }
  .contact-list svg { width: 13px; height: 13px; flex: none; }
</style>
</head>
<body>
  <section class="card card--front" aria-label="Business card front">
    <div class="brand-front">
      <span class="brand-ring" aria-hidden="true"></span>
      <span class="brand-name">Ridge + Studio Ltd</span>
    </div>
    <p class="front-web">www.rplusd.co.nz</p>
    <div class="member">
      <span class="member-badge" role="img" aria-label="BKTW membership badge"></span>
      <span class="member-label">Professional<br>Member</span>
    </div>
    <span class="lbp-badge" role="img" aria-label="Licensed building practitioner badge"></span>
  </section>

  <section class="card card--back" aria-label="Business card back">
    <div class="brand-back">
      <span class="brand-ring" aria-hidden="true"></span>
      <span class="brand-name">Ridge + Studio Ltd</span>
    </div>
    <span class="divider" aria-hidden="true"></span>
    <div class="contact">
      <h1 class="person-name">MARK DELFORD</h1>
      <p class="person-title">Architectural designer<br>&amp; Design LBP</p>
      <ul class="contact-list">
        <li>
          <svg viewBox="0 0 16 16" aria-hidden="true"><path d="M3 1h3l1.5 4-2 1.2a9 9 0 0 0 4.3 4.3L11 8.5l4 1.5v3a2 2 0 0 1-2 2A12 12 0 0 1 1 3a2 2 0 0 1 2-2z" fill="#fff"/></svg>
          02 5163 2290
        </li>
        <li>
          <svg viewBox="0 0 16 16" aria-hidden="true"><rect x="1" y="3" width="14" height="10" fill="none" stroke="#fff" stroke-width="1.6"/><path d="M1 3l7 6 7-6" fill="none" stroke="#fff" stroke-width="1.6"/></svg>
          mark@rplusd.co.nz
        </li>
        <li>
          <svg viewBox="0 0 16 16" aria-hidden="true"><circle cx="8" cy="8" r="7" fill="none" stroke="#fff" stroke-width="1.4"/><ellipse cx="8" cy="8" rx="3" ry="7" fill="none" stroke="#fff" stroke-width="1.2"/><path d="M1 8h14" stroke="#fff" stroke-width="1.2"/></svg>
          www.rplusd.co.nz
        </li>
      </ul>
    </div>
  </section>
</body>
</html>
```